New site for parent-to-parent advice in spanish requieres Wordpress design

Nidoluz.com ("time for child" in spanish) is a web site dedicated to give support from father to father in order to attend small babies and childs. The core idea is that divorced, single or widow male parents can get advice from other parents on attending our kids alone, as for short term visits or as single parents. It must be fun and easy to navigate, simple, practical and male-oriented. The site will be in spanish and Mexico and Latin-america market. Some subcategories will be ages of kids (toddlers, kids, preadolescents, adolescents; Bebés, Niños, Preadolescentes, Adolescentes) and other will be the father situation (widows, singles, divorced or even married; Viudos, Solteros, Divorciados, Casados).
Updates

Project Deadline Extended
Reason: As some of your questions are if it includes Wordpress Code and the answer is yes, we are recibed request to extend the deadline to workdays in order to can get the code over an unpdated designs. Thanks.

Target Market(s)

Divorced, single or widow male parents can get advice from other parents on attending our kids alone, as for short term visits or as single parents. The site will be in spanish an Latin-America oriented.

Industry/Entity Type

It Support

Requirements
Must have
• Nidoluz.com as the name of the site.
Space for banners well identified, in order to sell publicity but to clearly states wich is advice from the team and what paid publicity.
Nice to have
• Penguins will be prefered as the site mascot or graphic elements, since Penguins are the only animal in which male parent keep in charge of the small ones alone for six months a year -view photo for reference, not necesarly for direct use-
Trinos and Amigonet buttons.

```html
<!DOCTYPE html>
<html lang="es">
<head>
<meta charset="utf-8">
<title>Nidoluz.com — Hijos por Edades</title>
<link rel="stylesheet" href="https://fonts.googleapis.com/css2?family=Bebas+Neue&family=Oswald:wght@400;500&family=Open+Sans:ital,wght@0,400;0,700;1,400&family=Sansita:wght@700&display=swap">
<style>
:root{
  --sky-top:#8fd0ef;
  --sky-bottom:#c8ebf9;
  --nav:#2e7fa3;
  --nav-active:#1f4f66;
  --cream:#fdf4dc;
  --ink:#222;
  --muted:#444;
  --panel:#5aafd2;
  --panel-dark:#2f84a9;
  --panel-border:#2a7397;
  --tips-band:#6f808e;
  --footer:#1f2b33;
  --ad-blue:#3b5998;
  --ad-green:#5aa33a;
  --link-blue:#2f8ec0;
  --red:#d93a2b;
  --white:#fff;
}
*{box-sizing:border-box;margin:0;padding:0}
html,body{width:839px;height:1200px;overflow:hidden;background:var(--cream)}
body{font-family:"Open Sans",Arial,sans-serif;color:var(--ink)}
.page{position:relative;width:839px;height:1200px;overflow:hidden;background:var(--cream)}
.abs{position:absolute}

/* header */
.site-header{left:0;top:0;width:839px;height:88px;background:linear-gradient(var(--sky-top),var(--sky-bottom))}
.brand{left:173px;top:8px;width:170px;height:76px;display:flex;align-items:center;gap:8px}
.brand-dot{width:34px;height:34px;border-radius:50%;background:#1e6f93;flex:none}
.brand-name{font-family:"Oswald",sans-serif;font-weight:500;font-size:24px;color:#1e6f93;letter-spacing:.5px}
.tagline{left:360px;top:28px;width:240px;font-family:"Oswald",sans-serif;font-weight:500;font-size:12.5px;line-height:16px;color:var(--white);text-transform:uppercase}
.social{display:flex;gap:4px}
.social-btn{width:34px;height:35px;border:1px solid #e8f4fb}
.social-a{background:#3b5998}
.social-b{background:#3fb2e6}
.header-social{left:596px;top:27px}

/* nav */
.main-nav{left:0;width:839px;height:23px;background:var(--nav);display:flex;justify-content:center;align-items:center;font-family:"Oswald",sans-serif;font-size:10.5px;color:var(--white);text-transform:uppercase}
.main-nav span{padding:0 8px;line-height:23px}
.main-nav .dot{padding:0;font-size:8px}
.main-nav .active{background:var(--nav-active)}

/* tips */
.tips{left:173px;top:117px;width:491px;height:60px}
.tips-title{position:absolute;left:4px;top:0;font-family:"Bebas Neue",sans-serif;font-size:26px;color:#222;line-height:26px}
.tips-band{position:absolute;left:0;top:22px;width:491px;height:38px;background:var(--tips-band);border-left:4px solid #4d5b66;color:var(--white);font-style:italic;font-size:8.4px;line-height:11px;text-align:center;padding:7px 26px 0}
.tips-arrows{position:absolute;right:2px;top:2px;display:flex;gap:2px}
.tips-arrows span{width:13px;height:13px;background:#eee;border:1px solid #999}

/* left column */
.column{left:173px;top:191px;width:324px;display:flex;flex-direction:column}

/* ads */
.ad-banner{width:324px;height:46px;background:var(--white);border:1px solid #c9d2e3;flex:none}
.ad-bar{height:17px;background:var(--ad-blue);color:var(--white);font-weight:700;font-size:11px;line-height:17px;padding-left:6px;position:relative}
.ad-mark{position:absolute;right:3px;top:3px;width:10px;height:10px;background:#c8d4ea}
.ad-body{display:flex;align-items:center;justify-content:space-between;padding:4px 6px;font-size:9px}
.ad-body b{color:#333}
.ad-body em{font-style:normal;color:var(--ad-blue);margin-left:6px}
.ad-btn{background:var(--ad-green);color:var(--white);font-size:8px;font-weight:700;padding:3px 6px;border-radius:2px}

/* article */
.section-title{font-family:"Oswald",sans-serif;font-weight:500;font-size:17px;line-height:22px;text-transform:uppercase;color:#1d1d1d;margin-top:8px}
.intro{font-size:8.8px;line-height:12px;color:var(--muted);margin-top:4px}
.intro p{margin-bottom:10px}
.intro p:last-child{margin-bottom:0}
.avatar{float:left;width:74px;height:74px;background:linear-gradient(#8fc4dc,#5aa3c6);margin:0 10px 6px 0;border:1px solid #7fb2cb}

.bar{height:17px;background:var(--panel);border:1px solid var(--panel-border);color:var(--white);font-family:"Oswald",sans-serif;font-size:10.5px;text-transform:uppercase;line-height:15px;padding-left:4px;display:flex;justify-content:space-between;align-items:center;flex:none}
.bar svg{margin-right:5px}
.thread{margin-top:12px}

.comments{background:var(--white);border:1px solid #cfd9df;border-top:0}
.comment{display:flex;flex-direction:column;min-height:52px;padding:2px 3px 1px;border-bottom:1px solid #d6dde2;font-size:8px;line-height:11.2px;color:#333}
.comment b{color:#111}
.comment-actions{display:flex;justify-content:flex-end;align-items:center;gap:6px;font-size:7.5px;line-height:10px;margin-top:auto;padding-top:1px}
.tweet{border:1px solid #aaa;background:#eef3f6;padding:0 3px;color:#333;font-weight:700}
.tweet-count{border:1px solid #aaa;padding:0 3px}
.votes{color:var(--link-blue)}
.like{color:var(--link-blue);display:flex;align-items:center;gap:2px}
.dislike{color:var(--red);display:flex;align-items:center;gap:2px}

.reply{margin-top:4px}
.form-label{font-size:10px;line-height:13px;font-weight:700;color:#111;margin-left:3px}
.form-hint{font-size:7px;color:var(--red);font-weight:400;margin-left:6px}
.field{background:var(--white);border:1px solid #bcc6cc}
.publish{align-self:flex-end;width:62px;height:24px;margin-top:6px;background:var(--panel-dark);color:var(--white);font-family:"Sansita",sans-serif;font-size:14px;text-align:center;line-height:24px}
.more{margin-top:15px;display:flex;flex-direction:column;gap:1px}
.column .ad-bottom{margin-top:9px}

/* sidebar */
.sidebar{left:508px;top:191px;width:157px;background:var(--panel);border:1px solid var(--panel-border)}
.side-head{background:var(--panel-dark);color:var(--white);font-family:"Sansita",sans-serif;font-size:16px;height:29px;line-height:29px;padding-left:8px}
.side-list{list-style:disc;padding:4px 0 5px 29px;color:var(--white);font-size:9.4px;line-height:16px}
.side-ad{left:508px;top:624px;width:157px;height:129px;background:var(--white);border:1px solid #c6d0d6;text-align:center;padding:5px 4px}
.side-ad h4{font-family:"Oswald",sans-serif;font-weight:500;font-size:15px;line-height:16px;color:#1f6fa8}
.side-ad .ad-small{font-size:6.5px;color:var(--red);line-height:8px;margin-top:3px}
.side-ad .ad-deal{font-family:"Oswald",sans-serif;font-size:10px;line-height:12px;color:#1f6fa8;margin-top:6px}
.ad-photo{display:inline-block;width:66px;height:38px;background:linear-gradient(#a57a4c,#6b4a2b);vertical-align:middle;margin-top:5px}
.ad-cta{display:inline-block;vertical-align:middle;margin-top:5px;margin-left:4px;background:#2a7fc0;color:var(--white);font-size:7px;font-weight:700;padding:4px 6px}

/* footer */
.footer-nav{top:997px}
.site-footer{left:0;top:1020px;width:839px;height:180px;background:var(--footer);color:var(--white)}
.foot-col{position:absolute;top:13px;font-size:7px;line-height:9.5px}
.foot-col h5{font-family:"Oswald",sans-serif;font-weight:500;font-size:8.5px;text-transform:uppercase;margin:0 0 6px}
.foot-col ul{list-style:disc;padding-left:18px;margin:-3px 0 10px}
.foot-brand{left:507px;top:13px;width:170px;height:80px;display:flex;align-items:center;gap:8px}
.foot-brand .brand-name{color:#5fb8e0;font-size:26px}
.foot-brand .brand-dot{background:#5fb8e0}
.legal{position:absolute;left:0;width:839px;text-align:center;font-size:7px;line-height:10px}
.legal span{margin:0 7px}
</style>
</head>
<body>
<div class="page">

  <header class="site-header abs">
    <div class="brand abs"><span class="brand-dot"></span><span class="brand-name">Nidoluz.com</span></div>
    <p class="tagline abs">Lorem ipsum dolor sit amet, consectetur adipiscing elit. Phasellus</p>
    <div class="social header-social abs"><span class="social-btn social-a"></span><span class="social-btn social-b"></span></div>
  </header>

  <nav class="main-nav abs" style="top:88px">
    <span>Inicio</span><span class="dot">•</span><span>Primeros Pasos</span><span class="dot">•</span><span>Padre a Padre</span><span class="dot">•</span><span class="active">Hijos por Edades</span><span class="dot">•</span><span>Situacion del Padre</span><span class="dot">•</span><span>Nosotros</span><span class="dot">•</span><span>Contactos</span>
  </nav>

  <section class="tips abs">
    <div class="tips-band">Lorem ipsum dolor sit amet, consectetur adipiscing elit. Vivamus nec sodales ligula. Aenean tincidunt vitae ante eget faucibus. Vivamus ac diam diam. Sed ac sapien cursus diam sagittis consequat sit amet sit amet lectus.</div>
    <h2 class="tips-title">Tips!</h2>
    <div class="tips-arrows"><span></span><span></span></div>
  </section>

  <div class="column abs">
    <aside class="ad-banner">
      <div class="ad-bar">amigonet<span class="ad-mark"></span></div>
      <div class="ad-body"><span><b>Crea tu perfil en Amigonet</b><em>Regístrate gratis hoy!</em></span><span class="ad-btn">Entrar</span></div>
    </aside>

    <main>
      <h1 class="section-title">Hijos por Edades</h1>
      <div class="intro">
        <div class="avatar" role="img" aria-label="Foto de perfil del autor"></div>
        <p>Lorem ipsum dolor sit amet, consectetur adipiscing elit. Vivamus nec sodales ligula. Aenean tincidunt vitae ante eget faucibus. Vivamus ac diam diam. Sed ac sapien cursus diam sagittis consequat sit amet sit amet lectus.</p>
        <p>Lorem ipsum dolor sit amet, consectetur adipiscing elit. Vivamus nec sodales ligula. Aenean tincidunt vitae ante eget faucibus. Vivamus ac diam diam. Sed ac sapien cursus diam sagittis consequat sit amet sit amet lectus.</p>
      </div>
    </main>

    <section class="thread">
      <div class="bar">Cual es la mejor manera de cambiar un pañal?<svg width="10" height="7" viewBox="0 0 10 7"><path d="M0 7L5 0L10 7Z" fill="#fff"/></svg></div>
      <div class="comments">
        <div class="comment"><p><b>Carlos:</b> Lorem ipsum dolor sit amet, consectetur adipiscing elit. Vivamus nec sodales ligula. Aenean tincidunt vitae ante eget faucibus. Vivamus ac diam diam. Sed ac sapien cursus diam sagittis consequat sit amet sit amet lectus.</p>
          <div class="comment-actions"><span class="tweet">Trinos</span><span class="tweet-count">46</span><span class="votes">+16 a favor</span><span class="like"><svg width="9" height="8" viewBox="0 0 9 8"><path d="M0 3h2v5H0zM3 3l2-3h1v3h3v2l-1 3H3z" fill="#2f8ec0"/></svg>me gusta</span><span class="dislike"><svg width="9" height="8" viewBox="0 0 9 8"><path d="M0 0h2v5H0zM3 5l2 3h1V5h3V3L8 0H3z" fill="#d93a2b"/></svg>no me gusta</span></div></div>
        <div class="comment"><p><b>Raul:</b> Lorem ipsum dolor sit amet, consectetur adipiscing elit. Vivamus nec sodales ligula. Aenean tincidunt vitae ante eget faucibus. Vivamus ac diam diam. Sed ac sapien cursus diam sagittis consequat sit amet sit amet lectus.</p>
          <div class="comment-actions"><span class="tweet">Trinos</span><span class="tweet-count">46</span><span class="votes">+12 a favor</span><span class="like"><svg width="9" height="8" viewBox="0 0 9 8"><path d="M0 3h2v5H0zM3 3l2-3h1v3h3v2l-1 3H3z" fill="#2f8ec0"/></svg>me gusta</span><span class="dislike"><svg width="9" height="8" viewBox="0 0 9 8"><path d="M0 0h2v5H0zM3 5l2 3h1V5h3V3L8 0H3z" fill="#d93a2b"/></svg>no me gusta</span></div></div>
        <div class="comment"><p><b>Eduardo:</b> Lorem ipsum dolor sit amet, consectetur adipiscing elit. Vivamus nec sodales ligula. Aenean tincidunt vitae ante eget faucibus. Vivamus ac diam diam. Sed ac sapien cursus diam sagittis consequat sit amet sit amet lectus.</p>
          <div class="comment-actions"><span class="tweet">Trinos</span><span class="tweet-count">46</span><span class="votes">+8 a favor</span><span class="like"><svg width="9" height="8" viewBox="0 0 9 8"><path d="M0 3h2v5H0zM3 3l2-3h1v3h3v2l-1 3H3z" fill="#2f8ec0"/></svg>me gusta</span><span class="dislike"><svg width="9" height="8" viewBox="0 0 9 8"><path d="M0 0h2v5H0zM3 5l2 3h1V5h3V3L8 0H3z" fill="#d93a2b"/></svg>no me gusta</span></div></div>
        <div class="comment"><p><b>Mauro:</b> Lorem ipsum dolor sit amet, consectetur adipiscing elit. Vivamus nec sodales ligula. Aenean tincidunt vitae ante eget faucibus. Vivamus ac diam diam. Sed ac sapien cursus diam sagittis consequat sit amet sit amet lectus.</p>
          <div class="comment-actions"><span class="tweet">Trinos</span><span class="tweet-count">46</span><span class="votes">+5 a favor</span><span class="like"><svg width="9" height="8" viewBox="0 0 9 8"><path d="M0 3h2v5H0zM3 3l2-3h1v3h3v2l-1 3H3z" fill="#2f8ec0"/></svg>me gusta</span><span class="dislike"><svg width="9" height="8" viewBox="0 0 9 8"><path d="M0 0h2v5H0zM3 5l2 3h1V5h3V3L8 0H3z" fill="#d93a2b"/></svg>no me gusta</span></div></div>
        <div class="comment"><p><b>Ramiro:</b> Lorem ipsum dolor sit amet, consectetur adipiscing elit. Vivamus nec sodales ligula. Aenean tincidunt vitae ante eget faucibus. Vivamus ac diam diam. Sed ac sapien cursus diam sagittis consequat sit amet sit amet lectus.</p>
          <div class="comment-actions"><span class="tweet">Trinos</span><span class="tweet-count">46</span><span class="votes">+2 a favor</span><span class="like"><svg width="9" height="8" viewBox="0 0 9 8"><path d="M0 3h2v5H0zM3 3l2-3h1v3h3v2l-1 3H3z" fill="#2f8ec0"/></svg>me gusta</span><span class="dislike"><svg width="9" height="8" viewBox="0 0 9 8"><path d="M0 0h2v5H0zM3 5l2 3h1V5h3V3L8 0H3z" fill="#d93a2b"/></svg>no me gusta</span></div></div>
        <div class="comment"><p><b>José:</b> Lorem ipsum dolor sit amet, consectetur adipiscing elit. Vivamus nec sodales ligula. Aenean tincidunt vitae ante eget faucibus. Vivamus ac diam diam. Sed ac sapien cursus diam sagittis consequat sit amet sit amet lectus.</p>
          <div class="comment-actions"><span class="tweet">Trinos</span><span class="tweet-count">46</span><span class="votes">+0 a favor</span><span class="like"><svg width="9" height="8" viewBox="0 0 9 8"><path d="M0 3h2v5H0zM3 3l2-3h1v3h3v2l-1 3H3z" fill="#2f8ec0"/></svg>me gusta</span><span class="dislike"><svg width="9" height="8" viewBox="0 0 9 8"><path d="M0 0h2v5H0zM3 5l2 3h1V5h3V3L8 0H3z" fill="#d93a2b"/></svg>no me gusta</span></div></div>
      </div>
    </section>

    <form class="reply">
      <p class="form-label">Nombre:</p>
      <div class="field" style="width:76px;height:11px;margin:1px 0 0 3px"></div>
      <p class="form-label" style="margin-top:5px">Respuesta:<span class="form-hint">(300 caracteres máximo)</span></p>
      <div class="field" style="width:324px;height:54px;margin-top:1px"></div>
    </form>
    <div class="publish">Publicar!</div>

    <div class="more">
      <div class="bar">Niños<svg width="10" height="7" viewBox="0 0 10 7"><path d="M0 0L5 7L10 0Z" fill="#fff"/></svg></div>
      <div class="bar">Preadolescentes<svg width="10" height="7" viewBox="0 0 10 7"><path d="M0 0L5 7L10 0Z" fill="#fff"/></svg></div>
      <div class="bar">Adolescentes<svg width="10" height="7" viewBox="0 0 10 7"><path d="M0 0L5 7L10 0Z" fill="#fff"/></svg></div>
    </div>

    <aside class="ad-banner ad-bottom">
      <div class="ad-bar">amigonet<span class="ad-mark"></span></div>
      <div class="ad-body"><span><b>Crea tu perfil en Amigonet</b><em>Regístrate gratis hoy!</em></span><span class="ad-btn">Entrar</span></div>
    </aside>
  </div>

  <nav class="sidebar abs">
    <h3 class="side-head">Primeros Pasos</h3>
    <ul class="side-list"><li>Lorem Ipsum</li><li>Dolor sit amet</li><li>Consectetur</li><li>Adipiscing elit</li></ul>
    <h3 class="side-head">Padre a Padre</h3>
    <ul class="side-list"><li>Lorem Ipsum</li><li>Dolor sit amet</li><li>Consectetur</li><li>Adipiscing elit</li></ul>
    <h3 class="side-head">Hijos por Edades</h3>
    <ul class="side-list"><li>Bebés</li><li>Niños</li><li>Preadolescentes</li><li>Adolescentes</li></ul>
    <h3 class="side-head">Situacion del Padre</h3>
    <ul class="side-list"><li>Viudos</li><li>Solteros</li><li>Divorciados</li><li>Casados</li></ul>
    <h3 class="side-head">Tips</h3>
  </nav>

  <aside class="side-ad abs">
    <h4>Apartamentos Temporales</h4>
    <p class="ad-small">EL MEJOR PRECIO EN LOS MEJORES APARTAMENTOS</p>
    <p class="ad-deal">LAS MEJORES OFERTAS EN TEMPORADA ALTA</p>
    <span class="ad-photo" role="img" aria-label="Foto de una habitación de apartamento"></span><span class="ad-cta">INFÓRMESE YA</span>
  </aside>

  <nav class="main-nav footer-nav abs">
    <span>Inicio</span><span class="dot">•</span><span>Primeros Pasos</span><span class="dot">•</span><span>Padre a Padre</span><span class="dot">•</span><span>Hijos por Edades</span><span class="dot">•</span><span>Situacion del Padre</span><span class="dot">•</span><span>Nosotros</span><span class="dot">•</span><span>Contactos</span>
  </nav>

  <footer class="site-footer abs">
    <div class="foot-col" style="left:173px">
      <h5>Inicio</h5>
      <h5>Primeros Pasos</h5>
      <ul><li>Lorem Ipsum</li><li>Dolor sit amet</li><li>Consectetur</li><li>Adipiscing elit</li></ul>
      <h5>Padre a Padre</h5>
      <ul><li>Lorem Ipsum</li><li>Dolor sit amet</li><li>Consectetur</li><li>Adipiscing elit</li></ul>
    </div>
    <div class="foot-col" style="left:299px">
      <h5>Hijos por Edades</h5>
      <ul><li>Bebés</li><li>Niños</li><li>Preadolescentes</li><li>Adolescentes</li></ul>
      <h5>Situacion del Padre</h5>
      <ul><li>Viudos</li><li>Solteros</li><li>Divorciados</li><li>Casados</li></ul>
    </div>
    <div class="foot-col" style="left:424px">
      <h5>Nosotros</h5>
      <h5>Contactos</h5>
      <div class="social"><span class="social-btn social-a"></span><span class="social-btn social-b"></span></div>
    </div>
    <div class="foot-brand abs"><span class="brand-dot"></span><span class="brand-name">Nidoluz.com</span></div>
    <p class="legal" style="top:157px"><span>Terms and Conditions</span><span>Privacy Policy</span><span>How It Works</span><span>Acceptable Use Policy</span></p>
    <p class="legal" style="top:167px">© 2013 Nidoluz.com. All rights reserved.</p>
  </footer>

</div>
</body>
</html>
```